Quality Monitoring Company Needs a New Site

We are an established company that has a fair number of clients but the site lacks current design standards that we'd like to keep up with. We'd like to mimic the same style of the site on plinkora.com, vetrumo.com, https://brindlecoffer.com/, etc. We'd also like to make sure the designer understands SEO Silos and how it effects the design elements. Attached is the structure that I'd like to follow for the pages. You don't need to design every single sub-page because they'll probably be fairly similar; however, I want to see at least 1 each. Please use the content on our current site for filler areas. Please try to do a good job of understanding what we do so you can use your best judgement on what is needed to be successful. Use our color scheme and the logo should be the side view but I included the AI just in case.
Updates

I am narrowing down on the field of designs that I have received. There are a lot of similarities between the designs I like and don't like. I'd also like to ensure that some of the inner pages get done in the next 5 days so I can see the creativity that is there as well. That is probably what is next -- getting a few inner pages completed so I can see what you can come up with (not based on our current website) because the current "front pages" are all so good and so close.

Industry/Entity Type

Telecommunications

Colors

Designer to choose colors to be used in the design.

Requirements
Must have
• SEO Silo Look and Feel
• Current Colors
Should not have
• No stockphotos whatsoever. NONE.

```html
<!DOCTYPE html>
<html lang="en">
<head>
<meta charset="utf-8">
<title>Vocalyst – Contact</title>
<link href="https://fonts.googleapis.com/css2?family=Poppins:wght@400;500;600;700&display=swap" rel="stylesheet">
<style>
:root{
  --navy:#0a2d57;
  --footer:#003059;
  --blue:#00b1ea;
  --page:#f5f7fb;
  --text:#3a4454;
  --muted:#9aa3ad;
  --line:#c9d3e0;
}
*{margin:0;padding:0;box-sizing:border-box}
html,body{width:1200px;height:990px;overflow:hidden}
body{font-family:"Poppins",sans-serif;background:var(--page);color:var(--text);position:relative}
.abs{position:absolute}
.brand{left:141px;top:62px;display:flex;align-items:center;gap:8px;font-size:21px;font-weight:500;color:var(--navy)}
.brand-dot{width:14px;height:14px;border-radius:50%;background:var(--blue)}
.nav{left:404px;top:78px;display:flex;gap:23.5px;font-size:12.5px;color:#2f3a4a}
.nav .active{color:var(--blue);font-weight:600}
.hotline{left:904px;top:64px;display:flex;align-items:center;gap:9px;font-size:14.5px;font-weight:700;color:var(--navy);letter-spacing:.3px}
.hotline-icon{width:38px;height:38px;border-radius:50%;background:var(--blue);display:flex;align-items:center;justify-content:center}
.heading{font-size:30px;font-weight:700;color:var(--navy);line-height:1}
.heading span{color:var(--blue);font-weight:400}
.rule{width:35px;height:2px;background:var(--blue)}
.tagline{left:144px;top:266px;font-size:13px;color:#555f6c;letter-spacing:.2px}
.info{left:141px;display:flex;gap:13px}
.info svg{flex:none;margin-top:4px}
.info h4{font-size:13px;font-weight:600;color:var(--navy);line-height:19px}
.info p{font-size:13px;line-height:19px;letter-spacing:.5px;color:#2f3a4a}
.card{left:599px;top:160px;width:459px;height:424px;background:#fff;border-radius:20px;box-shadow:0 18px 40px rgba(0,110,200,.08)}
.field{left:636px;width:388px;height:39px;border:1px solid var(--line);border-radius:3px;background:#fff;display:flex;align-items:center;padding-left:13px;gap:13px;font-size:12.5px;color:var(--muted)}
.field.msg{height:95px;align-items:flex-start;padding-top:11px}
.submit{left:637px;top:513px;width:127px;height:35px;border-radius:18px;background:var(--blue);color:#fff;font-size:13.5px;font-weight:600;letter-spacing:.8px;display:flex;align-items:center;justify-content:center}
.footer{left:0;top:721px;width:1200px;height:269px;background:var(--footer);color:#fff}
.f-title{font-size:17px;font-weight:600;color:var(--blue)}
.links{font-size:11.5px;line-height:20.5px;color:#fff}
.f-item{display:flex;gap:10px;font-size:12.5px;line-height:23px;letter-spacing:.3px;color:#fff}
.f-item svg{flex:none;margin-top:5px}
.f-brand{left:932px;top:815px;display:flex;align-items:center;gap:10px;font-size:24px;font-weight:500;color:#fff}
.f-brand i{width:30px;height:30px;border-radius:50%;background:var(--blue);display:block}
.divider{left:139px;top:942px;width:919px;height:1px;background:#1c4a75}
.copy{left:0;width:1200px;top:957px;text-align:center;font-size:12.5px;color:#fff}
</style>
</head>
<body>

<div class="abs brand"><span class="brand-dot"></span>Vocalyst</div>

<nav class="abs nav">
  <span>Home</span><span>Services</span><span>Industries</span><span>Pricing</span><span class="active">Team</span><span>Blog</span><span>Contact Us</span>
</nav>

<div class="abs hotline">
  <span class="hotline-icon"><svg width="16" height="16" viewBox="0 0 24 24"><path fill="#fff" d="M6.6 10.8a15 15 0 0 0 6.6 6.6l2.2-2.2a1 1 0 0 1 1-.25 11.4 11.4 0 0 0 3.6.57 1 1 0 0 1 1 1V20a1 1 0 0 1-1 1A17 17 0 0 1 3 4a1 1 0 0 1 1-1h3.5a1 1 0 0 1 1 1c0 1.25.2 2.45.57 3.57a1 1 0 0 1-.25 1z"/></svg></span>
  800-555-0173
</div>

<h1 class="abs heading" style="left:144px;top:199px">Connect <span>Us</span></h1>
<div class="abs rule" style="left:144px;top:243px"></div>
<p class="abs tagline">Connect with us. Visit us. Work with us.</p>

<div class="abs info" style="top:313px">
  <svg width="32" height="32" viewBox="0 0 32 32" fill="none" stroke="var(--blue)" stroke-width="1.4"><path d="M8 3l4 6-2.5 2.5a14 14 0 0 0 11 11L23 20l6 4-2 4c-11 1-24-12-23-23z"/><path d="M19 4a9 9 0 0 1 9 9M19 8a5 5 0 0 1 5 5"/></svg>
  <div><h4>Phone</h4><p>800-555-0173</p></div>
</div>

<div class="abs info" style="top:395px">
  <svg width="34" height="38" viewBox="0 0 34 38" fill="none" stroke="var(--blue)" stroke-width="1.4"><path d="M17 30S7 19 7 12a10 10 0 0 1 20 0c0 7-10 18-10 18z"/><circle cx="17" cy="12" r="5"/><path d="M9 27H4l-3 8h32l-3-8h-5M6 31h6M22 31h6"/></svg>
  <div><h4>Address</h4><p>4820 Meridian Ave.<br>Harlow Park, CA 91400</p></div>
</div>

<div class="abs info" style="top:497px">
  <svg width="34" height="34" viewBox="0 0 34 34" fill="none" stroke="var(--blue)" stroke-width="1.4"><path d="M1 13l16-11 16 11v19H1z"/><path d="M1 13l16 11 16-11M1 32l12-10M33 32L21 22"/><rect x="8" y="5" width="18" height="12" fill="#fff"/><circle cx="17" cy="11" r="3"/></svg>
  <div><h4>Email</h4><p style="letter-spacing:.2px">hello@vocalyst.com</p></div>
</div>

<section class="abs card"></section>
<h2 class="abs heading" style="left:640px;top:199px">Inquiry <span>Now</span></h2>
<div class="abs rule" style="left:640px;top:243px"></div>

<div class="abs field" style="top:261px"><svg width="12" height="12" viewBox="0 0 24 24"><circle cx="12" cy="7" r="5" fill="var(--blue)"/><path d="M3 23a9 9 0 0 1 18 0z" fill="var(--blue)"/></svg>Name</div>
<div class="abs field" style="top:308px"><svg width="12" height="12" viewBox="0 0 24 24"><path fill="var(--blue)" d="M6.6 10.8a15 15 0 0 0 6.6 6.6l2.2-2.2a1 1 0 0 1 1-.25 11.4 11.4 0 0 0 3.6.57 1 1 0 0 1 1 1V20a1 1 0 0 1-1 1A17 17 0 0 1 3 4a1 1 0 0 1 1-1h3.5a1 1 0 0 1 1 1c0 1.25.2 2.45.57 3.57a1 1 0 0 1-.25 1z"/></svg>Phone</div>
<div class="abs field" style="top:356px"><svg width="13" height="11" viewBox="0 0 26 20"><path fill="var(--blue)" d="M0 2h26v16H0z"/><path d="M0 3l13 9 13-9" fill="none" stroke="#fff" stroke-width="2"/></svg>Email</div>
<div class="abs field msg" style="top:404px"><svg width="13" height="13" viewBox="0 0 24 24" fill="none" stroke="var(--blue)" stroke-width="2"><path d="M11 4H3v17h17v-8"/><path d="M18 2l4 4-10 10H8v-4z"/></svg>Message</div>
<div class="abs submit">SUBMIT</div>

<footer class="abs footer"></footer>
<h3 class="abs f-title" style="left:139px;top:778px">Quick Links</h3>
<div class="abs links" style="left:139px;top:812px">Home<br>Services<br>System Details<br>Pricing</div>
<div class="abs links" style="left:294px;top:812px">Team<br>Blog<br>Contact Us<br>Login</div>

<h3 class="abs f-title" style="left:460px;top:778px">Contact Us</h3>
<div class="abs f-item" style="left:462px;top:812px">
  <svg width="11" height="15" viewBox="0 0 22 30"><path fill="#fff" d="M11 0a11 11 0 0 1 11 11c0 8-11 19-11 19S0 19 0 11A11 11 0 0 1 11 0z"/><circle cx="11" cy="11" r="4" fill="var(--footer)"/></svg>
  <span>4820 Meridian Ave.<br>Harlow Park, CA 91400</span>
</div>
<div class="abs f-item" style="left:660px;top:812px">
  <svg width="14" height="14" viewBox="0 0 24 24"><path fill="#fff" d="M6.6 10.8a15 15 0 0 0 6.6 6.6l2.2-2.2a1 1 0 0 1 1-.25 11.4 11.4 0 0 0 3.6.57 1 1 0 0 1 1 1V20a1 1 0 0 1-1 1A17 17 0 0 1 3 4a1 1 0 0 1 1-1h3.5a1 1 0 0 1 1 1c0 1.25.2 2.45.57 3.57a1 1 0 0 1-.25 1z"/></svg>
  <span>800-555-0173</span>
</div>
<div class="abs f-item" style="left:660px;top:847px">
  <svg width="14" height="11" viewBox="0 0 26 20"><path fill="#fff" d="M0 2h26v16H0z"/><path d="M0 3l13 9 13-9" fill="none" stroke="var(--footer)" stroke-width="2"/></svg>
  <span>Hello@Vocalyst.com</span>
</div>

<div class="abs f-brand"><i></i>Vocalyst</div>

<div class="abs divider"></div>
<p class="abs copy">Copyright © 2019 VOCALYST. All Rights Reserved.</p>

</body>
</html>
```